Web Calculator design Housing Investment

We have a web calculator that needs to be fixed from a design perspective. The key tasks are:<br/>1. Selecting icons / pictures / colours for the various steps<br/>2. Designing navigation between calculator steps<br/>3. Making suggestions for chart design. The limitation is that the charts are all using the Vextra API (the same charts that Vextra Grids use).<br/><br/>There are four entry screens and then a result screen. See attached PDF for screenshots. You can see our website at https://larkhollowfunds.com for our corporate colours and style.

Target Market(s)

Real Estate Investors

Industry/Entity Type

Financial Planning

Number of Pages Required

1 page

Font styles to use
Sans Serif
Other font styles liked:
• Ubuntu

Colors
86cae7
3176b5
0455a3
ffffff

Requirements
Must have
• New Icons
• Suggested design for navigation
• Suggested design for charts

```html
<!DOCTYPE html>
<html lang="en">
<head>
<meta charset="utf-8">
<title>Housing Investment Calculator</title>
<link rel="stylesheet" href="https://fonts.googleapis.com/css2?family=Poppins:ital,wght@0,400;0,500;1,500&display=swap">
<style>
  :root {
    --bg: #ebebeb;
    --accent: #e2262b;
    --ink: #2b2b2b;
    --muted: #3a3a3a;
    --track: #d6d6d6;
    --card: #ffffff;
    --radio-off: #cfcfcf;
    --unit-tone: #8fc8ea;
    --house-tone: #cfcfcf;
  }
  * { box-sizing: border-box; margin: 0; padding: 0; }
  html, body { width: 1200px; height: 613px; overflow: hidden; }
  body {
    background: var(--bg);
    font-family: "Poppins", sans-serif;
    color: var(--ink);
    position: relative;
  }
  .title {
    position: absolute; top: 42px; left: 0; width: 1200px;
    text-align: center; font-style: italic; font-weight: 500;
    font-size: 35px; letter-spacing: 0.3px;
  }
  .title .initial { color: var(--accent); }
  .title-rule {
    position: absolute; top: 106px; left: 147px; width: 905px; height: 2px;
    background: var(--accent);
  }
  .steps { position: absolute; top: 138px; left: 0; width: 1200px; height: 90px; }
  .step {
    position: absolute; transform: translateX(-50%);
    display: flex; flex-direction: column; align-items: center;
    font-size: 15.5px; color: var(--muted); white-space: nowrap;
  }
  .step svg { width: 58px; height: 56px; margin-bottom: 14px; }
  .step svg * { fill: none; stroke: var(--ink); stroke-width: 2; stroke-linejoin: round; stroke-linecap: round; }
  .step.is-active { color: var(--accent); }
  .step.is-active svg * { stroke: var(--accent); }
  .progress {
    position: absolute; top: 250px; left: 147px; width: 905px; height: 13px;
    background: var(--track); border-radius: 7px;
  }
  .progress-fill {
    width: 135px; height: 100%; border-radius: 7px;
    background: repeating-linear-gradient(-60deg, var(--accent) 0 6px, #f07074 6px 9px);
  }
  .progress-marker {
    position: absolute; top: 239px; left: 276px;
    width: 0; height: 0;
    border-left: 5px solid transparent; border-right: 5px solid transparent;
    border-top: 7px solid var(--accent);
  }
  .question {
    position: absolute; top: 290px; left: 0; width: 1200px;
    text-align: center; font-size: 16.5px; color: var(--muted);
  }
  .choice {
    position: absolute; top: 331px; width: 200px; height: 172px;
    background: var(--card); border-radius: 3px;
    box-shadow: 0 1px 3px rgba(0,0,0,0.08);
  }
  .choice.unit { left: 388px; }
  .choice.property { left: 610px; }
  .choice-art { position: absolute; top: 16px; left: 42px; width: 116px; height: 106px; border-radius: 4px; }
  .unit .choice-art { background: linear-gradient(180deg, var(--unit-tone), #4a90c8); }
  .property .choice-art { background: linear-gradient(180deg, #e4e4e4, var(--house-tone)); }
  .choice-label {
    position: absolute; top: 133px; left: 0; width: 100%;
    display: flex; justify-content: center; align-items: center; gap: 12px;
    font-size: 17px; color: var(--muted);
  }
  .radio { width: 19px; height: 19px; border-radius: 50%; background: var(--radio-off); }
  .radio.is-on { background: #e5e5e5; display: flex; align-items: center; justify-content: center; }
  .radio.is-on::after { content: ""; width: 12px; height: 12px; border-radius: 50%; background: var(--accent); }
  .nav {
    position: absolute; top: 540px; left: 0; width: 1200px;
    display: flex; justify-content: center; align-items: center; gap: 9px;
    font-size: 13px; color: var(--ink);
  }
  .nav svg { width: 44px; height: 18px; }
  .nav svg * { fill: none; stroke: #555; stroke-width: 1; }
</style>
</head>
<body>
  <h1 class="title"><span class="initial">H</span>ousing <span class="initial">I</span>nvestment <span class="initial">C</span>alculator</h1>
  <div class="title-rule"></div>

  <div class="steps">
    <div class="step is-active" style="left:203px">
      <svg viewBox="0 0 58 56"><path d="M26 22 L42 6 L57 22"/><path d="M30 18 V48 H55 V20"/><rect x="37" y="26" width="5" height="5"/><rect x="46" y="26" width="5" height="5"/><rect x="37" y="35" width="5" height="5"/><rect x="46" y="35" width="5" height="5"/><path d="M3 30 L14 22 L30 22"/><rect x="3" y="30" width="27" height="18"/><path d="M7 36 H26 M7 41 H26 M7 46 H26"/></svg>
      <span>Property Type</span>
    </div>
    <div class="step" style="left:378px">
      <svg viewBox="0 0 58 56"><path d="M29 40 C20 30 16 24 16 17 A13 13 0 0 1 42 17 C42 24 38 30 29 40 Z"/><path d="M23 19 L29 13 L35 19 V24 H23 Z"/><ellipse cx="29" cy="46" rx="22" ry="6"/></svg>
      <span>Property Location</span>
    </div>
    <div class="step" style="left:579px">
      <svg viewBox="0 0 58 56"><path d="M12 4 H40 V26 M32 50 H12 V4"/><path d="M18 18 L26 11 L34 18 V26 H18 Z"/><path d="M18 32 H30 M18 38 H28 M18 44 H26"/><circle cx="40" cy="38" r="8"/><path d="M46 44 L53 51"/></svg>
      <span>Property Valuation</span>
    </div>
    <div class="step" style="left:801px">
      <svg viewBox="0 0 58 56"><path d="M6 26 L29 5 L52 26"/><path d="M11 22 V50 M47 22 V50"/><path d="M29 13 V15 M26 23 C26 19 33 19 33 22 C33 26 26 25 26 29 C26 32 33 32 33 29 M29 32 V35"/><path d="M15 44 L24 36 L31 41 L43 30 M39 30 H43 V34"/><path d="M3 50 H55"/></svg>
      <span>Your Property Forecast</span>
    </div>
    <div class="step" style="left:993px">
      <svg viewBox="0 0 58 56"><rect x="24" y="4" width="28" height="44"/><rect x="29" y="9" width="18" height="8"/><path d="M30 23 H34 M38 23 H42 M30 29 H34 M38 29 H42 M30 35 H34 M38 35 H42 M46 23 V40"/><path d="M4 34 L17 24 L30 34"/><path d="M8 31 V50 H28 V34"/><rect x="15" y="40" width="6" height="10"/></svg>
      <span>Calculator</span>
    </div>
  </div>

  <div class="progress"><div class="progress-fill"></div></div>
  <div class="progress-marker"></div>

  <p class="question">What type of property would you like to compare ?</p>

  <div class="choice unit">
    <div class="choice-art" role="img" aria-label="Illustration of a blue apartment tower with trees"></div>
    <div class="choice-label"><span class="radio is-on"></span>Unit</div>
  </div>
  <div class="choice property">
    <div class="choice-art" role="img" aria-label="Illustration of a detached house with a garage"></div>
    <div class="choice-label"><span class="radio"></span>Property</div>
  </div>

  <nav class="nav">
    <span>Previous</span>
    <svg viewBox="0 0 44 18"><rect x="0.5" y="0.5" width="20" height="17"/><rect x="23.5" y="0.5" width="20" height="17"/><path d="M5 9 H17 M5 9 L9 5 M5 9 L9 13"/><path d="M27 9 H39 M39 9 L35 5 M39 9 L35 13"/></svg>
    <span>Next</span>
  </nav>
</body>
</html>
```